Drone service provider needs a brilliant web design

I need a responsive web design for a new drone service company. Pelham Drone Solutions provides turnkey solutions to capture, process, and deliver actionable aerial data to customers. The design should communicate a professional company that is safe, legal and insured. I included our logo design and business card designs for reference.
*content to be supplied after design selected

Target Market(s)

We serve telecommunications, construction, government, utility infrastructure, insurance and other industries.

Industry/Entity Type

Industrial

Number of Pages Required

5+ page

Colors

Designer to choose colors to be used in the design.

Requirements
Must have
• The design should highlight professional services to include Inspections, Mapping, Consulting and Training. The site should include aerial images and video to compliment the services offered. The landing page must include following sections in order: HOME, SERVICES, ABOUT, DEMO REEL, CLIENTS, CONTACT FORM, and social media buttons (Facebook, LinkedIn, Twitter, YouTube, Instagram). Contact: 615-382-9041 info@pelhamdronesolutions-example.com Smyrna, TN
• Sitemap:
• 6 pages: Home, Inspections, Mapping, Training, Consulting, About
• HOME (Landing Page)
• • Header with logo and tab links (Home, Services, About, Contact)
• • 'CAPTURE. PROCESS. DELIVER.' tagline and 'CONTACT US' button displayed within aerial image of drone over city or construction site
• • Services section with icons, text and read more link to page
• • About section with photo and text with three icons for SAFE. LEGAL. INSURED.
• • Demo reel
• • Clients logos shown scrolling horizontally
• • Contact form
• • Footer with logo, phone, email, social media buttons
• SERVICES (4 different pages)
• • Inspections
• • Mapping
• • Consulting
• • Training
• ABOUT page
• • Company
• • Partners
• • Certifications & Associations
• • Careers
• CONTACT linked to bottom of landing page
• Would you like to receive the newsletter? Yes or No Drop-down list
Nice to have
• Photos of KVR Marlin or Corvex inspecting infrastructure, buildings, construction sites, etc. A photo of one or two pilots in vest and helmet. Free stock photos preferred but would purchase the right photo that's more relevant.
• website references:
• https://www.quillrotor-example.com/
• https://www.brentfieldworks-example.com/services
• https://www.tomaro-example.com/
• http://gantrymetric-example.com/
• http://lumbrook-example.com/
• http://fennotics-example.com/
• https://www.grebe-example.io/
Should not have
• not an aerial photography or videography service business, no blog or newsletter

```html
<!DOCTYPE html>
<html lang="en">
<head>
<meta charset="utf-8">
<title>Pelham Drone Solutions</title>
<link rel="stylesheet" href="https://fonts.googleapis.com/css2?family=Audiowide&family=Lato:wght@400;700&display=swap">
<style>
:root{
  --blue:#1a8fdb;
  --blue-dark:#1579bd;
  --ink:#1b1b1b;
  --text:#555a60;
  --muted:#8a8f94;
  --white:#ffffff;
  --gray-band:#e6e6e6;
  --footer-bar:#dcdcdc;
  --line:#8d9196;
  --dot:#111111;
}
*{box-sizing:border-box;margin:0;padding:0}
html,body{width:1200px;height:3056px;overflow:hidden}
body{position:relative;background:var(--white);font-family:"Lato",sans-serif;color:var(--text)}

/* header */
.site-header{position:absolute;left:0;top:0;width:1200px;height:92px;background:var(--white);z-index:5}
.brand{position:absolute;left:118px;top:22px;width:220px;font-weight:700;font-size:22px;line-height:24px;color:var(--ink);letter-spacing:1px;text-transform:uppercase}
.main-nav{position:absolute;left:458px;top:40px;display:flex;gap:34px;font-size:15px;color:var(--ink);text-transform:uppercase}
.main-nav .active{color:var(--blue)}

/* hero */
.hero{position:absolute;left:0;top:92px;width:1200px;height:601px;z-index:3;
  background:linear-gradient(160deg,#6b6a4a 0%,#4f5a36 30%,#7a6b4a 55%,#3f4f2c 80%,#5c5a3e 100%);
  clip-path:polygon(0 0,100% 0,100% 519px,50% 100%,0 519px)}
.hero::after{content:"";position:absolute;inset:0;background:rgba(20,20,15,.35)}
.hero-play{position:absolute;left:560px;top:168px;z-index:2}
.hero-title{position:absolute;left:0;top:270px;width:1200px;text-align:center;z-index:2;color:var(--white);
  font-family:"Audiowide",sans-serif;font-size:36px;font-weight:400;letter-spacing:2px}
.hero-sub{position:absolute;left:0;top:318px;width:1200px;text-align:center;z-index:2;color:var(--white);
  font-family:"Audiowide",sans-serif;font-size:25px;letter-spacing:2px}

/* about */
.about{position:absolute;left:0;top:560px;width:1200px;height:540px;
  background:linear-gradient(180deg,#f4f4f6 0%,#ffffff 35%,#fbf3f0 70%,#efe6ee 100%)}
.about-kicker{position:absolute;left:0;top:182px;width:1200px;text-align:center;font-family:"Audiowide",sans-serif;font-weight:400;font-size:22px;color:var(--ink);letter-spacing:1px}
.about-title{position:absolute;left:0;top:212px;width:1200px;text-align:center;font-family:"Audiowide",sans-serif;font-weight:400;font-size:32px;color:var(--ink);letter-spacing:1px}
.about-text{position:absolute;left:214px;top:272px;width:772px;text-align:center;font-size:16px;line-height:25px;color:var(--text)}
.btn-dark{position:absolute;left:530px;top:418px;width:148px;height:40px;background:#111;color:var(--white);font-size:15px;font-weight:700;display:flex;align-items:center;justify-content:center}

/* services */
.services{position:absolute;left:0;top:1100px;width:1200px;height:458px;background:var(--blue)}
.services-notch{position:absolute;left:570px;top:0}
.section-title{font-family:"Audiowide",sans-serif;font-weight:400;font-size:26px;letter-spacing:1px;text-align:center;position:absolute;left:0;width:1200px}
.services .section-title{top:44px;color:var(--white)}
.service-card{position:absolute;top:98px;width:233px;height:309px;border:1px solid rgba(255,255,255,.75);text-align:center;color:var(--white)}
.service-icon{position:absolute;left:64px;top:32px}
.service-name{position:absolute;left:0;top:150px;width:100%;font-size:22px;font-weight:400}
.service-desc{position:absolute;left:28px;top:183px;width:177px;font-size:11px;line-height:20px;color:rgba(255,255,255,.85)}
.service-more{position:absolute;left:0;top:258px;width:100%;font-size:12px;font-weight:700}

/* gallery */
.gallery-title{top:1596px;color:var(--ink)}
.tile{position:absolute}
.tile .play{position:absolute;left:50%;top:50%;transform:translate(-50%,-50%)}

/* contact */
.contact{position:absolute;left:0;top:2196px;width:1200px;height:442px;
  background:linear-gradient(135deg,#dedede 0%,#f4f4f4 45%,#e2e2e2 100%)}
.contact .section-title{top:60px;color:var(--ink)}
.field{position:absolute;font-size:16px;color:#5a5e63;border-bottom:1px solid var(--line);padding-bottom:8px}
.btn-outline{position:absolute;left:511px;top:326px;width:194px;height:40px;border:2px solid var(--blue);color:var(--blue);font-size:15px;font-weight:700;display:flex;align-items:center;justify-content:center;letter-spacing:1px}

/* social band */
.social-band{position:absolute;left:0;top:2638px;width:1200px;height:82px;background:var(--blue)}
.social-label{position:absolute;left:291px;top:28px;font-family:"Audiowide",sans-serif;font-size:23px;color:var(--white);letter-spacing:1px}
.social-dot{position:absolute;top:16px;width:49px;height:49px;border-radius:50%;background:var(--dot)}

/* footer */
.footer{position:absolute;left:0;top:2720px;width:1200px;height:268px;background:var(--white)}
.footer-brand{position:absolute;left:130px;top:64px;width:250px;font-weight:700;font-size:26px;line-height:30px;color:var(--ink);letter-spacing:1px;text-transform:uppercase}
.footer-col{position:absolute;top:56px}
.footer-col h4{font-size:15px;font-weight:700;color:var(--ink);margin-bottom:14px;text-transform:uppercase}
.footer-col li{list-style:none;font-size:14px;color:var(--muted);line-height:31px}
.contact-line{display:flex;align-items:center;gap:8px;font-size:14px;color:var(--muted);line-height:31px;white-space:nowrap}
.copyright{position:absolute;left:0;top:2988px;width:1200px;height:68px;background:var(--footer-bar);text-align:center;line-height:68px;font-size:12px;color:#666}
</style>
</head>
<body>

<header class="site-header">
  <div class="brand">Pelham Drone Solutions</div>
  <nav class="main-nav">
    <span class="active">Home</span><span>About Us</span><span>Services</span><span>Blogs</span><span>Videos</span><span>Contact Us</span>
  </nav>
</header>

<section class="hero" role="img" aria-label="Aerial view of patchwork farm fields">
  <svg class="hero-play" width="80" height="80" viewBox="0 0 80 80" aria-hidden="true">
    <circle cx="40" cy="40" r="37" fill="none" stroke="#fff" stroke-width="3"/>
    <path d="M33 27 L54 40 L33 53 Z" fill="none" stroke="#fff" stroke-width="3" stroke-linejoin="round"/>
  </svg>
  <h1 class="hero-title">CAPTURE. PROCESS. DELIVERY</h1>
  <p class="hero-sub">MORBI MAURIS VIVERRA GRAVIDA</p>
</section>

<section class="about" role="img" aria-label="Soft backdrop of a white drone flying above clouds">
  <h2 class="about-kicker">ABOUT PELHAM</h2>
  <h3 class="about-title">DRONE SOLUTION</h3>
  <p class="about-text">We make businesses look great online with amazing websites, engaging social media posts, top search positions and reputation management. Get your FREE reputation snapshot report here. Norrow Design Company is a full-service website development, search engine optimization, software development, social media management and hosting company.</p>
  <span class="btn-dark">Learn More</span>
</section>

<section class="services">
  <svg class="services-notch" width="60" height="20" viewBox="0 0 60 20" aria-hidden="true"><path d="M0 0 H60 L30 20 Z" fill="#fff"/></svg>
  <h2 class="section-title">OUR SERVICES</h2>

  <article class="service-card" style="left:122px">
    <svg class="service-icon" width="104" height="104" viewBox="0 0 104 104" aria-hidden="true">
      <path d="M52 4 L94 28 V76 L52 100 L10 76 V28 Z" fill="none" stroke="#fff" stroke-width="3"/>
      <circle cx="47" cy="47" r="17" fill="none" stroke="#fff" stroke-width="3"/>
      <path d="M59 59 L72 72" stroke="#fff" stroke-width="5" stroke-linecap="round"/>
      <path d="M40 47 H54 M47 40 V54" stroke="#fff" stroke-width="2"/>
    </svg>
    <h3 class="service-name">Inspection</h3>
    <p class="service-desc">Close checks of towers, roofs and bridges with clear reports</p>
    <span class="service-more">READ MORE</span>
  </article>

  <article class="service-card" style="left:363px">
    <svg class="service-icon" width="104" height="104" viewBox="0 0 104 104" aria-hidden="true">
      <path d="M52 4 L94 28 V76 L52 100 L10 76 V28 Z" fill="none" stroke="#fff" stroke-width="3"/>
      <path d="M52 74 C44 62 38 54 38 46 A14 14 0 0 1 66 46 C66 54 60 62 52 74 Z" fill="none" stroke="#fff" stroke-width="3"/>
      <circle cx="52" cy="46" r="5" fill="none" stroke="#fff" stroke-width="3"/>
    </svg>
    <h3 class="service-name">Mapping</h3>
    <p class="service-desc">Accurate aerial maps and surveys for sites of every scale</p>
    <span class="service-more">READ MORE</span>
  </article>

  <article class="service-card" style="left:605px">
    <svg class="service-icon" width="104" height="104" viewBox="0 0 104 104" aria-hidden="true">
      <path d="M52 4 L94 28 V76 L52 100 L10 76 V28 Z" fill="none" stroke="#fff" stroke-width="3"/>
      <rect x="30" y="34" width="30" height="20" rx="3" fill="#fff"/>
      <path d="M36 54 L34 62 L44 54 Z" fill="#fff"/>
      <rect x="50" y="46" width="26" height="18" rx="3" fill="none" stroke="#fff" stroke-width="3"/>
      <path d="M68 64 L72 70 L62 64" fill="none" stroke="#fff" stroke-width="3"/>
    </svg>
    <h3 class="service-name">Consulting</h3>
    <p class="service-desc">Guidance on programs, rules and equipment for your own team</p>
    <span class="service-more">READ MORE</span>
  </article>

  <article class="service-card" style="left:845px">
    <svg class="service-icon" width="104" height="104" viewBox="0 0 104 104" aria-hidden="true">
      <path d="M52 4 L94 28 V76 L52 100 L10 76 V28 Z" fill="none" stroke="#fff" stroke-width="3"/>
      <rect x="34" y="32" width="38" height="26" fill="none" stroke="#fff" stroke-width="3"/>
      <path d="M40 50 L48 43 L54 47 L64 38" fill="none" stroke="#fff" stroke-width="2.5"/>
      <path d="M53 58 V68 M45 72 L53 64 L61 72" fill="none" stroke="#fff" stroke-width="3"/>
    </svg>
    <h3 class="service-name">Training</h3>
    <p class="service-desc">Hands-on pilot courses that build safe and skilled crews</p>
    <span class="service-more">READ MORE</span>
  </article>
</section>

<h2 class="section-title gallery-title">VIDEOS &amp; GALLERY</h2>

<div class="tile" style="left:0;top:1660px;width:332px;height:230px;background:linear-gradient(180deg,#c89a5a 0%,#6d6a5e 50%,#2e3a3a 100%)" role="img" aria-label="City skyline at sunset with highway, video">
  <svg class="play" width="66" height="66" viewBox="0 0 66 66" aria-hidden="true"><circle cx="33" cy="33" r="33" fill="#fff"/><path d="M26 20 L47 33 L26 46 Z" fill="#222"/></svg>
</div>
<div class="tile" style="left:0;top:1894px;width:332px;height:302px;background:linear-gradient(160deg,#3f8f6a 0%,#3fb1c9 40%,#6fc6d8 100%)" role="img" aria-label="Marina with boats in turquoise water"></div>

<div class="tile" style="left:336px;top:1660px;width:528px;height:352px;background:linear-gradient(135deg,#6e6a5a 0%,#8a8170 40%,#4e5a40 100%)" role="img" aria-label="Overhead view of a residential neighbourhood, video">
  <svg class="play" width="66" height="66" viewBox="0 0 66 66" aria-hidden="true"><circle cx="33" cy="33" r="33" fill="#fff"/><path d="M26 20 L47 33 L26 46 Z" fill="#222"/></svg>
</div>
<div class="tile" style="left:336px;top:2016px;width:261px;height:180px;background:linear-gradient(135deg,#7fae3e,#5d9a2e)" role="img" aria-label="Green crop fields from above"></div>
<div class="tile" style="left:603px;top:2016px;width:261px;height:180px;background:radial-gradient(circle at 45% 40%,#9fcf6a 0%,#3f7a2e 45%,#244a1c 100%)" role="img" aria-label="Golf green surrounded by trees"></div>

<div class="tile" style="left:868px;top:1660px;width:332px;height:177px;background:linear-gradient(135deg,#2f5a26 0%,#4f8a3a 50%,#e8d9a6 75%,#4aa3b0 100%)" role="img" aria-label="Forest meeting a sandy beach"></div>
<div class="tile" style="left:868px;top:1843px;width:332px;height:173px;background:linear-gradient(180deg,#b9c9d6 0%,#7f99a8 45%,#c8b8a0 100%)" role="img" aria-label="Coastal city by the sea"></div>
<div class="tile" style="left:868px;top:2020px;width:332px;height:176px;background:linear-gradient(135deg,#6f9a4e 0%,#4f7a34 60%,#a8b890 100%)" role="img" aria-label="Drone flying over green hills, video">
  <svg class="play" width="66" height="66" viewBox="0 0 66 66" aria-hidden="true"><circle cx="33" cy="33" r="33" fill="#fff"/><path d="M26 20 L47 33 L26 46 Z" fill="#222"/></svg>
</div>

<section class="contact">
  <h2 class="section-title">CONTACT FORM</h2>
  <div class="field" style="left:163px;top:148px;width:251px">Your Name</div>
  <div class="field" style="left:452px;top:148px;width:251px">Email address</div>
  <div class="field" style="left:739px;top:148px;width:253px">Phone Number</div>
  <div class="field" style="left:163px;top:202px;width:829px;height:92px">Write a message here</div>
  <span class="btn-outline">SEND NOW</span>
</section>

<section class="social-band">
  <span class="social-label">STAY IN TOUCH</span>
  <span class="social-dot" style="left:532px" aria-label="Social link 1"></span>
  <span class="social-dot" style="left:589px" aria-label="Social link 2"></span>
  <span class="social-dot" style="left:646px" aria-label="Social link 3"></span>
  <span class="social-dot" style="left:703px" aria-label="Social link 4"></span>
  <span class="social-dot" style="left:760px" aria-label="Social link 5"></span>
</section>

<footer class="footer">
  <div class="footer-brand">Pelham Drone Solutions</div>
  <div class="footer-col" style="left:442px">
    <h4>Quick Links</h4>
    <ul><li>Home</li><li>About Us</li><li>Our Services</li><li>Products</li></ul>
  </div>
  <div class="footer-col" style="left:638px">
    <h4>Resources</h4>
    <ul><li>Portfolio</li><li>Testimonials</li><li>Clients</li><li>Contact Us</li></ul>
  </div>
  <div class="footer-col" style="left:833px">
    <h4>Contact Us</h4>
    <div class="contact-line">
      <svg width="18" height="18" viewBox="0 0 24 24" aria-hidden="true"><path d="M6 3 L10 3 L11 8 L8 10 C9.5 13 11 14.5 14 16 L16 13 L21 14 L21 18 C21 20 19 21 17 21 C9 20 4 15 3 7 C3 5 4 3 6 3 Z" fill="none" stroke="#222" stroke-width="2"/></svg>
      615-382-9041
    </div>
    <div class="contact-line">
      <svg width="18" height="18" viewBox="0 0 24 24" aria-hidden="true"><rect x="3" y="5" width="18" height="14" fill="none" stroke="#222" stroke-width="2"/><path d="M3 6 L12 13 L21 6" fill="none" stroke="#222" stroke-width="2"/></svg>
      office@pelhamdronesolutions-example.com
    </div>
    <div class="contact-line">
      <svg width="18" height="18" viewBox="0 0 24 24" aria-hidden="true"><circle cx="12" cy="12" r="10" fill="#222"/><path d="M2 12 H22 M12 2 C7 7 7 17 12 22 M12 2 C17 7 17 17 12 22" fill="none" stroke="#fff" stroke-width="1.5"/></svg>
      www.pelhamdronesolutions-example.com
    </div>
  </div>
</footer>

<div class="copyright">© 2017 Company Name &nbsp;All right reserved</div>

</body>
</html>
```